1876 Basins & Spouts Business Card

I'm wanting to get a business card designed. Our business is 1876 Basins & Spouts
Details for the card:

1876 Basins & Spouts
Name: Harold Vesk
Email: harold@1876basinsandspouts.com.au
Website: www.1876basinsandspouts.com.au
Mobile: 0438 260 947
Phone: 02 7481 3926

Font of Basins & Spouts is called Snell Roundhand. Not sue what font logo text is.

I'm thinking two sided but it doesn't have to be.

```html
<!DOCTYPE html>
<html lang="en">
<head>
<meta charset="UTF-8">
<title>1876 Basins &amp; Spouts – Business Card</title>
<link rel="stylesheet" href="https://fonts.googleapis.com/css2?family=Lato:wght@400;700&family=Kaushan+Script&display=swap">
<style>
  :root {
    --backdrop: #1f1f1f;
    --card: #ffffff;
    --ink: #111111;
    --ink-soft: #333333;
    --ornament-light: #ececec;
    --ornament-mid: #d2d2d2;
  }
  * { box-sizing: border-box; margin: 0; padding: 0; }
  html, body {
    width: 1200px; height: 900px; overflow: hidden;
    background: var(--backdrop);
  }
  .canvas {
    position: relative; width: 1200px; height: 900px;
  }
  .card {
    position: absolute; left: 100px; top: 164px;
    width: 1000px; height: 572px;
    background: var(--card);
    overflow: hidden;
    font-family: "Lato", sans-serif;
    color: var(--ink);
  }
  .ornament {
    position: absolute; right: 30px; top: 40px;
    width: 520px; height: 430px;
    background: radial-gradient(ellipse at 60% 50%, var(--ornament-mid) 0%, var(--ornament-light) 45%, rgba(255,255,255,0) 72%);
  }
  .brand {
    position: absolute; left: 90px; top: 140px;
    display: flex; align-items: center; gap: 18px;
  }
  .brand-mark {
    width: 72px; height: 72px; border-radius: 50%;
    border: 2px solid var(--ink);
    flex: none;
  }
  .brand-name {
    font-size: 32px; font-weight: 400; color: var(--ink);
    line-height: 1;
  }
  .brand-tagline {
    margin-top: 8px;
    font-size: 13px; color: var(--ink-soft); letter-spacing: 0.2px;
  }
  .person-name {
    position: absolute; left: 180px; top: 300px;
    font-family: "Kaushan Script", cursive;
    font-size: 42px; font-weight: 400; color: var(--ink);
  }
  .contact-list {
    position: absolute; left: 230px; top: 372px;
    list-style: none;
  }
  .contact-item {
    display: flex; align-items: center; gap: 16px;
    height: 40px;
    font-size: 21px; color: var(--ink-soft); letter-spacing: 0.3px;
  }
  .contact-icon {
    width: 30px; height: 30px; border-radius: 50%;
    background: var(--ink);
    display: flex; align-items: center; justify-content: center;
    flex: none;
  }
  .website {
    position: absolute; left: 230px; top: 500px;
    font-size: 22px; font-weight: 700; color: var(--ink);
    letter-spacing: 0.3px;
  }
</style>
</head>
<body>
<div class="canvas">
  <section class="card">
    <div class="ornament" role="img" aria-label="Light grey flowing floral vine ornament with leaves and curling tendrils"></div>

    <header class="brand">
      <div class="brand-mark"></div>
      <div>
        <div class="brand-name">1876 Basins &amp; Spouts</div>
        <div class="brand-tagline">Pairing heritage elegance with everyday durability</div>
      </div>
    </header>

    <h1 class="person-name">Harold Vesk</h1>

    <ul class="contact-list">
      <li class="contact-item">
        <span class="contact-icon">
          <svg width="14" height="18" viewBox="0 0 14 18"><rect x="2" y="1" width="10" height="16" rx="2" fill="none" stroke="#fff" stroke-width="1.6"/><circle cx="7" cy="14" r="1" fill="#fff"/></svg>
        </span>
        0438 260 947
      </li>
      <li class="contact-item">
        <span class="contact-icon">
          <svg width="18" height="16" viewBox="0 0 18 16"><path d="M2 5 Q9 0 16 5 L14 7 L12 5 L6 5 L4 7 Z" fill="#fff"/><rect x="4" y="8" width="10" height="6" rx="1" fill="#fff"/></svg>
        </span>
        02 7481 3926
      </li>
      <li class="contact-item">
        <span class="contact-icon">
          <svg width="18" height="13" viewBox="0 0 18 13"><rect x="1" y="1" width="16" height="11" fill="none" stroke="#fff" stroke-width="1.5"/><path d="M1 1 L9 7 L17 1" fill="none" stroke="#fff" stroke-width="1.5"/></svg>
        </span>
        harold@1876basinsandspouts.com.au
      </li>
    </ul>

    <div class="website">www.1876basinsandspouts.com.au</div>
  </section>
</div>
</body>
</html>
```